Bookkeeping business needs a digital and print flyer

We need a flyer to promote our virtual bookkeeping services to small and mid-sized businesses in the United States. We want the content and design of the flyer to be consistent with our website: www.brightlanebookkeeping.example. We would like both a print version and a digital version of the flyer.

```html
<!DOCTYPE html>
<html lang="en">
<head>
<meta charset="utf-8">
<title>Bright Lane Bookkeeping – Virtual Bookkeeping Flyer</title>
<link href="https://fonts.googleapis.com/css2?family=Montserrat:wght@300;400;600;700;800&family=Poppins:wght@300;400;500;600;700&display=swap" rel="stylesheet">
<style>
  :root {
    --ink: #1c1c1c;
    --dark: #222222;
    --dark-soft: #2e2e2e;
    --yellow: #f9c232;
    --yellow-light: #fbd56b;
    --yellow-pale: #fde9a6;
    --white: #ffffff;
    --text: #2a2a2a;
  }
  * { margin: 0; padding: 0; box-sizing: border-box; }
  html, body { width: 937px; height: 1200px; overflow: hidden; background: var(--white); }
  .flyer {
    position: relative; width: 937px; height: 1200px; overflow: hidden;
    font-family: 'Poppins', sans-serif; color: var(--text); background: var(--white);
  }
  .abs { position: absolute; }

  /* Header */
  .header-band {
    left: 0; top: 0; width: 937px; height: 423px;
    background: linear-gradient(120deg, #262626 0%, #1b1b1b 55%, #242424 100%);
  }
  .brand {
    left: 52px; top: 52px; display: flex; align-items: center; gap: 14px;
    color: var(--white); font-family: 'Poppins', sans-serif; font-weight: 300;
  }
  .brand-name { font-size: 30px; line-height: 1; letter-spacing: 1px; }
  .brand-name small { display: block; font-size: 13px; letter-spacing: 2px; margin-top: 4px; text-align: right; }
  .brand-mark { width: 40px; height: 40px; border: 2px solid var(--white); border-radius: 50%; }

  .headline { left: 52px; top: 160px; font-family: 'Montserrat', sans-serif; line-height: 1; }
  .headline .thin { display: block; color: var(--white); font-weight: 300; font-size: 37px; letter-spacing: 9px; }
  .headline .bold-line { display: block; color: var(--yellow); font-weight: 800; font-size: 32px; margin-top: 5px; }
  .headline .bold-line .light { font-weight: 300; }
  .accent-dash { left: 52px; top: 288px; width: 24px; height: 5px; background: var(--yellow); }
  .tagline {
    left: 52px; top: 324px; color: var(--white);
    font-family: 'Montserrat', sans-serif; font-weight: 600; font-size: 15px; line-height: 21px;
  }

  /* Photo stack */
  .frame-back { left: 451px; top: 56px; width: 405px; height: 504px; background: var(--yellow-light); }
  .frame-mid { left: 465px; top: 69px; width: 405px; height: 505px; background: var(--yellow); }
  .photo-main {
    left: 478px; top: 79px; width: 409px; height: 508px; border: 3px solid var(--white);
    background: linear-gradient(150deg, #c9c6c2 0%, #a7acb8 40%, #8d98ad 70%, #e3e2df 100%);
  }

  /* Services */
  .services-title {
    left: 52px; top: 441px; color: var(--yellow);
    font-family: 'Montserrat', sans-serif; font-weight: 800; font-size: 29px; letter-spacing: 6px;
  }
  .services-sub {
    left: 52px; top: 488px; color: var(--ink);
    font-family: 'Montserrat', sans-serif; font-weight: 700; font-size: 14.5px; line-height: 21px;
  }
  .check-list { list-style: none; }
  .check-list li {
    position: relative; padding-left: 22px; font-size: 12.6px; line-height: 14.5px; font-weight: 400;
  }
  .check-list li svg { position: absolute; left: 0; top: 1px; width: 12px; height: 12px; }
  .services-list { left: 52px; top: 557px; width: 400px; color: var(--text); }
  .services-list li { margin-bottom: 17.5px; }

  /* Benefits */
  .charge-line {
    left: 456px; top: 612px; color: var(--ink);
    font-family: 'Montserrat', sans-serif; font-weight: 700; font-size: 14.5px; line-height: 21px;
  }
  .benefit-box {
    left: 451px; top: 696px; width: 486px; height: 330px;
    background: linear-gradient(160deg, #272727 0%, #1d1d1d 60%, #2a2a2a 100%);
  }
  .benefit-label {
    left: 471px; top: 675px; width: 360px; height: 32px; background: var(--yellow);
    color: var(--ink); font-family: 'Montserrat', sans-serif; font-weight: 700; font-size: 17px;
    display: flex; align-items: center; justify-content: center;
  }
  .benefit-list { left: 490px; top: 733px; color: var(--white); }
  .benefit-list li { margin-bottom: 17.5px; }

  /* Footer */
  .footer-wave { left: 0; top: 985px; width: 937px; height: 215px; }
  .portrait {
    left: 0; top: 962px; width: 222px; height: 238px;
    border-radius: 90px 90px 0 0;
    background: linear-gradient(180deg, #e7d6c6 0%, #f3f0ec 55%, #ffffff 100%);
  }
  .cta {
    left: 238px; top: 1052px; color: var(--ink); font-family: 'Montserrat', sans-serif; line-height: 1;
  }
  .cta .cta-top { display: block; font-weight: 500; font-size: 20.5px; letter-spacing: 0.5px; }
  .cta .cta-main { display: block; font-weight: 700; font-size: 20.5px; margin-top: 4px; letter-spacing: 0.5px; }
  .phone {
    left: 238px; top: 1115px; display: flex; align-items: center; gap: 6px;
    font-family: 'Montserrat', sans-serif; font-weight: 800; font-size: 29px; color: var(--ink);
  }
  .phone svg { width: 22px; height: 22px; }
  .contact { left: 552px; display: flex; align-items: center; gap: 6px; font-size: 13px; color: var(--ink); }
  .contact svg { width: 14px; height: 14px; }
  .contact-location { top: 1051px; }
  .contact-email { top: 1077px; }
  .web-bar {
    left: 544px; top: 1116px; width: 393px; height: 30px; background: var(--dark);
    display: flex; align-items: center; padding-left: 10px;
    color: var(--white); font-size: 11.5px; letter-spacing: 1.3px;
  }
  .web-bar strong { color: var(--yellow); font-weight: 700; }
</style>
</head>
<body>
<svg width="0" height="0" style="position:absolute" aria-hidden="true">
  <defs>
    <symbol id="tick" viewBox="0 0 12 12">
      <circle cx="6" cy="6" r="6" fill="#f9c232"/>
      <path d="M3.2 6.2 L5.2 8.1 L8.9 4.2" fill="none" stroke="#ffffff" stroke-width="1.5" stroke-linecap="round" stroke-linejoin="round"/>
    </symbol>
  </defs>
</svg>

<main class="flyer">
  <div class="abs header-band" role="img" aria-label="Dark desk scene with laptop and plant"></div>

  <div class="abs brand">
    <div class="brand-name">BRIGHT LANE<small>BOOKKEEPING</small></div>
    <div class="brand-mark"></div>
  </div>

  <h1 class="abs headline">
    <span class="thin">VIRTUAL</span>
    <span class="bold-line">BOOKKEEPING <span class="light">FOR</span></span>
    <span class="bold-line">SMALL BUSINESS</span>
  </h1>
  <div class="abs accent-dash"></div>
  <p class="abs tagline">Build Your Business by Focusing<br>on What You Love</p>

  <div class="abs frame-back"></div>
  <div class="abs frame-mid"></div>
  <div class="abs photo-main" role="img" aria-label="Stressed business owner holding his head at a desk covered in papers and receipts"></div>

  <h2 class="abs services-title">SERVICES</h2>
  <p class="abs services-sub">Bookkeeping Tailored to YOUR<br>Business Needs</p>
  <ul class="abs check-list services-list">
    <li><svg><use href="#tick"/></svg>Catch-up and clean-up services</li>
    <li><svg><use href="#tick"/></svg>Transaction importation and categorization</li>
    <li><svg><use href="#tick"/></svg>Monthly reconciliation of all accounts,</li>
    <li><svg><use href="#tick"/></svg>including assets and loans.</li>
    <li><svg><use href="#tick"/></svg>Monthly video conference</li>
    <li><svg><use href="#tick"/></svg>Annual tax-prep package sent to your<br>preparer</li>
    <li><svg><use href="#tick"/></svg>A/R &amp; A/P</li>
    <li><svg><use href="#tick"/></svg>Payroll coordination</li>
    <li><svg><use href="#tick"/></svg>1099s</li>
    <li><svg><use href="#tick"/></svg>Bill pay and receipt management</li>
    <li><svg><use href="#tick"/></svg>Budgeting</li>
    <li><svg><use href="#tick"/></svg>Monthly financial reports (Balance Sheet,<br>Income Statement, Cash Flow)</li>
  </ul>

  <p class="abs charge-line">Take charge of your business and concentrate<br>on your strengths to become its hero!</p>
  <div class="abs benefit-box" role="img" aria-label="Dim office desk with calculator and papers"></div>
  <div class="abs benefit-label">Outsource your bookkeeping!</div>
  <ul class="abs check-list benefit-list">
    <li><svg><use href="#tick"/></svg>Take back your time</li>
    <li><svg><use href="#tick"/></svg>Do more of what you love</li>
    <li><svg><use href="#tick"/></svg>Focus on your strengths and what you do best</li>
    <li><svg><use href="#tick"/></svg>Confidently make business decisions</li>
    <li><svg><use href="#tick"/></svg>Sail through tax time</li>
    <li><svg><use href="#tick"/></svg>Save over the expense of a full-time employee</li>
    <li><svg><use href="#tick"/></svg>Pay yourself more</li>
    <li><svg><use href="#tick"/></svg>Experience financial peace</li>
  </ul>

  <svg class="abs footer-wave" viewBox="0 0 937 215" preserveAspectRatio="none" aria-hidden="true">
    <path d="M0 20 C150 -2 300 38 470 26 S800 -4 937 8 L937 215 L0 215 Z" fill="var(--yellow-pale)"/>
    <path d="M0 40 C160 18 330 56 500 42 S820 14 937 28 L937 215 L0 215 Z" fill="var(--yellow)"/>
  </svg>

  <div class="abs portrait" role="img" aria-label="Portrait of the bookkeeper in white shirt and tie, arms crossed"></div>

  <p class="abs cta"><span class="cta-top">REQUEST YOU</span><span class="cta-main">FREE CONSULTATION</span></p>
  <div class="abs phone">
    <svg viewBox="0 0 24 24" aria-hidden="true">
      <circle cx="12" cy="12" r="11" fill="none" stroke="#1c1c1c" stroke-width="2"/>
      <path d="M8.2 6.5c.4-.3 1-.2 1.3.2l1.3 1.9c.3.4.2 1-.2 1.3l-.8.6c.6 1.4 1.6 2.5 3 3.2l.6-.8c.3-.4.9-.5 1.3-.2l1.9 1.3c.4.3.5.9.2 1.3l-.8 1.1c-.5.7-1.4.9-2.2.6-3.2-1.2-5.5-3.6-6.6-6.8-.3-.8 0-1.7.6-2.2z" fill="#1c1c1c"/>
    </svg>
    <span>308-555-0147</span>
  </div>

  <div class="abs contact contact-location">
    <svg viewBox="0 0 16 16" aria-hidden="true"><circle cx="8" cy="8" r="8" fill="#1c1c1c"/><path d="M8 3.3a3 3 0 0 0-3 3c0 2.2 3 5.5 3 5.5s3-3.3 3-5.5a3 3 0 0 0-3-3z" fill="#f9c232"/><circle cx="8" cy="6.3" r="1.1" fill="#1c1c1c"/></svg>
    <span>Maple Falls, NE</span>
  </div>
  <div class="abs contact contact-email">
    <svg viewBox="0 0 16 16" aria-hidden="true"><circle cx="8" cy="8" r="8" fill="#1c1c1c"/><rect x="4" y="5.2" width="8" height="5.6" fill="none" stroke="#f9c232" stroke-width="1"/><path d="M4 5.4 L8 8.4 L12 5.4" fill="none" stroke="#f9c232" stroke-width="1"/></svg>
    <span>mara@brightlanebookkeeping.example</span>
  </div>
  <div class="abs web-bar">www.<strong>brightlanebookkeeping</strong>.example</div>
</main>
</body>
</html>
```